Oriel Photography Business Card

I need a business card designed for a photography business based in Perth, Western Australia called Oriel Photography.

We specialise in wedding, event photography and portrait photography.

The business card must borrow the style of the attached logo.

The hex codes for the colours in the logo are:
#ED1D85 - Pink
#89C23E - Green
#37282F - Black

The name on the card will be:
Name: Tobrian
Phone: 0417395268
Website: www.orielphotography.example.com.au
Facebook: orielphotography

I am open and happy to accept creative concepts.

I’d like some space at the back for writing notes and appointment details.

```html
<!DOCTYPE html>
<html lang="en">
<head>
<meta charset="utf-8">
<title>Oriel Photography – Business Card</title>
<link rel="stylesheet" href="https://fonts.googleapis.com/css2?family=Cinzel:wght@400;600&family=Open+Sans:ital,wght@0,400;0,600;0,700;1,400&display=swap">
<style>
  :root{
    --pink:#ED1D85;
    --green:#89C23E;
    --ink:#37282F;
    --grey:#5a5a5e;
    --rule:#c9c9cc;
    --field:#8a8a8e;
    --stage:#e8e8ed;
    --card:#ffffff;
  }
  *{box-sizing:border-box;margin:0;padding:0}
  html,body{width:1200px;height:987px;overflow:hidden}
  body{
    background:var(--stage);
    font-family:"Open Sans",Arial,sans-serif;
    color:var(--ink);
    display:flex;align-items:center;justify-content:center;gap:50px;
  }
  .card{
    position:relative;
    width:540px;height:310px;
    background:var(--card);
    border-radius:26px;
    box-shadow:0 10px 30px rgba(0,0,0,.12);
    overflow:hidden;
  }

  /* Front */
  .brand{
    position:absolute;left:0;right:0;top:48px;
    display:flex;flex-direction:column;align-items:center;gap:14px;
  }
  .brand-mark{width:62px;height:62px;border-radius:50%;background:var(--pink)}
  .brand-name{
    font-size:15px;letter-spacing:11px;text-transform:uppercase;
    color:var(--grey);font-weight:400;padding-left:11px;
  }
  .front-rule{
    position:absolute;left:40px;right:40px;top:172px;height:1px;
    background:linear-gradient(90deg,transparent,var(--rule) 15%,var(--rule) 85%,transparent);
  }
  .person{
    position:absolute;left:0;right:0;top:186px;text-align:center;
    color:var(--pink);font-weight:700;font-size:22px;letter-spacing:1px;text-transform:uppercase;
  }
  .contacts{
    position:absolute;left:0;right:0;top:222px;
    display:flex;flex-direction:column;align-items:center;gap:4px;
    font-size:14px;color:var(--ink);
  }
  .contact{display:flex;align-items:center;gap:7px}
  .contact svg{width:13px;height:13px;flex:none}

  /* Back */
  .back{padding:26px 30px}
  .back-mark{
    position:absolute;left:50%;top:50%;width:170px;height:170px;
    margin:-85px 0 0 -85px;border-radius:50%;
    background:var(--pink);opacity:.06;
  }
  .back-title{
    position:relative;text-align:center;
    font-family:"Cinzel",Georgia,serif;color:var(--pink);
    font-size:19px;font-weight:600;letter-spacing:1px;margin-bottom:14px;
  }
  .row{position:relative;display:flex;align-items:flex-end;gap:8px;font-size:13px;color:var(--grey);margin-bottom:12px}
  .line{flex:1;border-bottom:1px solid var(--field);height:14px}
  .box{border:1px solid var(--field);border-radius:3px;height:22px;background:transparent}
  .box.wide{width:120px}
  .days{position:relative;display:flex;align-items:center;justify-content:space-between;margin:16px 0 14px}
  .day{display:flex;align-items:center;gap:6px;font-size:12px;font-weight:700;color:var(--grey)}
  .day .box{width:28px;height:20px}
  .note{position:relative;text-align:center;font-style:italic;font-size:13px;color:var(--grey)}
</style>
</head>
<body>

<section class="card front" aria-label="Card front">
  <div class="brand">
    <span class="brand-mark" aria-hidden="true"></span>
    <span class="brand-name">Oriel Photography</span>
  </div>
  <div class="front-rule"></div>
  <p class="person">Tobrian</p>
  <ul class="contacts">
    <li class="contact">
      <svg viewBox="0 0 14 14" aria-hidden="true"><circle cx="7" cy="7" r="7" fill="var(--green)"/><path d="M4.6 3.6l1.3 1.6-.7.9c.5 1 1.3 1.8 2.3 2.3l.9-.7 1.6 1.3-.6 1.3c-2.8-.3-5-2.5-5.3-5.3z" fill="#fff"/></svg>
      <span>0417395268</span>
    </li>
    <li class="contact">
      <svg viewBox="0 0 14 14" aria-hidden="true"><rect width="14" height="14" rx="2" fill="var(--grey)"/></svg>
      <span>orielphotography</span>
    </li>
    <li class="contact">
      <svg viewBox="0 0 14 14" aria-hidden="true"><circle cx="7" cy="7" r="6.2" fill="none" stroke="var(--green)" stroke-width="1.4"/><path d="M1 7h12M7 1c-2.4 3-2.4 9 0 12M7 1c2.4 3 2.4 9 0 12" fill="none" stroke="var(--green)" stroke-width="1"/></svg>
      <span>www.orielphotography.example.com.au</span>
    </li>
  </ul>
</section>

<section class="card back" aria-label="Card back">
  <span class="back-mark" aria-hidden="true"></span>
  <h2 class="back-title">Your Appointment</h2>
  <div class="row"><span>Name :</span><span class="line"></span></div>
  <div class="row"><span>Date :</span><span class="line"></span></div>
  <div class="row">
    <span>Next Appointment</span><span class="box wide"></span>
    <span>Time :</span><span class="box wide"></span><span>am / pm</span>
  </div>
  <div class="days">
    <span class="day">MON<span class="box"></span></span>
    <span class="day">TUE<span class="box"></span></span>
    <span class="day">WED<span class="box"></span></span>
    <span class="day">THU<span class="box"></span></span>
    <span class="day">FRI<span class="box"></span></span>
    <span class="day">SAT<span class="box"></span></span>
  </div>
  <p class="note">We appreciate a 24 hr. notice for cancellations</p>
</section>

</body>
</html>
```